Give Gold Kite an Online Presence!

Gold Kite Property Maintenance is an Australian Owned property maintenance company who needs a stand out online presence.

GK maintains many buildings and sites and wants to appeal to a corporate professional market with their brand new website. GK is essentially a handyman service offering all maintenance services to home owners, office managers, real estate agents and strata managers.

The Website:
We need a corporate website that appeals to our broader customer base (property owners, property managers, office managers) the copy is being written by a professional so use filler text for now.

Things that we want:
Home page that sets us apart and appeals to the corporate and residential market. The home page needs to not focus on either the residential or commercial market. The home page should focus on our logo and branding. We have a logo already and it is attached to the brief, please use it and try to consider the colour pallette that goes with it. Whilst we want the site to appear strong and manly it is important to remember that 95% of our customers are female so we need the site to be appealing to women. Women need to believe that we are strong, dependable and trustworthy.
We'd like a quote page and potentially also the ability to get a quote from the home page (please don't put it in if it ruins the overall feel of the home page)
An "about us" page
A contact us page
A blog that's built in (we don't want to link to an external blog)
(overall we'd expect to have 6 or 7 pages total)

The site will also need coding - we expect this to be done in a separate project but need you to consider a few things about the coding side of things.

It needs to be iPhone and iPad compatible.

We'd like you to suggest the best CMS that you would use or if you would suggest not using a CMS please let us know with your submissions.

Target Market(s)

Property owners, office managers and property managers who need maintenance on buildings (So all of them)

Industry/Entity Type

Property Maintenance

Requirements
Must have
• Our Logo
Home page
About Us
Residential
Commercial
Real Estate/Strata
Contact Us/Quote
Blog
Nice to have
• Quote form included in home page
Movement on the home page at least
Should not have
• other logos, too much colour
NO FLASH

```html
<!DOCTYPE html>
<html lang="en">
<head>
<meta charset="utf-8">
<title>Gold Kite Property Maintenance</title>
<link rel="stylesheet" href="https://fonts.googleapis.com/css2?family=Fira+Sans+Condensed:ital,wght@0,400;0,500;1,400;1,500&family=Arimo:wght@400;700&display=swap">
<style>
:root{
  --orange:#f39221;
  --text:#5a5a5a;
  --heading:#585858;
  --nav-dark:#2c2c2c;
  --nav-light:#4a4a4a;
  --panel-border:#d6d6d6;
  --rule:#d0d0d0;
  --link:#1f4fa3;
}
*{margin:0;padding:0;box-sizing:border-box}
html,body{width:1200px;height:1066px;overflow:hidden}
body{position:relative;font-family:Arimo,Arial,sans-serif;color:var(--text);
  background:linear-gradient(#e4e4e4 0,#f7f7f7 120px,#fafafa 300px,#ececec 340px,#f4f4f4 420px,#fff 700px);}
.abs{position:absolute}
.brand{left:206px;top:34px;display:flex;align-items:flex-start;gap:7px;font:500 15px/17px "Fira Sans Condensed",sans-serif;color:var(--orange);z-index:3}
.brand-mark{width:14px;height:14px;margin-top:2px;background:var(--orange);flex:none}
.contact-line{left:856px;font:400 16px "Fira Sans Condensed",sans-serif;color:#666;display:flex;align-items:center;gap:8px}
.top-divider{left:837px;top:22px;width:1px;height:48px;background:#d4d4d4}
.nav{left:180px;top:87px;width:835px;height:32px;border-radius:4px;background:linear-gradient(var(--nav-light),var(--nav-dark));box-shadow:0 1px 2px rgba(0,0,0,.3)}
.nav a,.foot a{position:absolute;font:700 8.5px Arimo,Arial,sans-serif;text-decoration:none;letter-spacing:.2px}
.nav a{color:#fff;top:11px}
.foot a{color:#8a8a8a;top:955px}
.h-script{font:italic 500 19px "Fira Sans Condensed",sans-serif;color:var(--heading);letter-spacing:-.3px}
.h-script em{font-style:italic;color:var(--orange)}
.intro{left:206px;top:194px;width:420px;font-size:10.5px;line-height:15.7px}
.intro p+p{margin-top:15.7px}
.hero-photo{left:657px;top:135px;width:345px;height:185px;border-radius:50% 50% 0 0/40% 40% 0 0;background:linear-gradient(135deg,#e9c7a3,#f2d64a 40%,#3f8f4e 70%,#ececec)}
.panel{left:179px;top:320px;width:837px;height:600px;background:#fff;border:1px solid var(--panel-border);border-radius:6px}
.rule{height:0;border-top:1px dotted var(--rule)}
.body-copy{font-size:10.5px;line-height:12.8px;width:430px}
.seal{left:592px;top:348px;width:66px;height:66px;border-radius:50%;background:radial-gradient(circle at 40% 35%,#ffc940,#e58a10)}
.thumb{top:521px;width:104px;height:76px;border:1px solid #d4d4d4;border-radius:2px;padding:3px;background:#fff}
.thumb span{display:block;width:100%;height:100%}
.quote{left:773px;top:359px;width:187px;height:214px;border:1px solid #d4d4d4;border-radius:4px;background:#fff}
.field{position:absolute;height:14px;border:1px solid #b8b8b8;background:#fff;font-size:9px;padding-left:3px;line-height:12px;color:#222}
.lbl{position:absolute;font-size:8px;color:#333}
.select{position:absolute;left:14px;top:130px;width:157px;height:15px;border:1px solid #b8b8b8;border-radius:3px;background:linear-gradient(#fff,#ddd);font-size:9px;padding-left:7px;line-height:13px;color:#222}
.select i{position:absolute;right:0;top:0;width:14px;height:13px;border-left:1px solid #b8b8b8;font-style:normal;font-size:7px;text-align:center}
.submit{position:absolute;left:14px;top:155px;width:62px;height:15px;background:linear-gradient(#f7a94b,#e97f1a);color:#fff;font:700 8.5px Arimo,sans-serif;text-align:center;line-height:15px}
.news-title{font:700 10.5px Arimo,sans-serif;color:#555;letter-spacing:.4px}
.news-text{font-size:10.5px;line-height:12.5px;width:205px}
.more{font-size:8px;color:var(--orange);text-decoration:underline}
.curl{left:905px;top:872px;width:111px;height:48px;background:linear-gradient(160deg,transparent 45%,#ececec 60%,#fff 75%);border-bottom-right-radius:6px}
</style>
</head>
<body>
<div class="abs brand"><span class="brand-mark"></span><span>GOLD KITE<br>PROPERTY MAINTENANCE</span></div>

<div class="abs top-divider"></div>
<div class="abs contact-line" style="top:20px">
  <svg width="16" height="16" viewBox="0 0 16 16"><circle cx="8" cy="8" r="7" fill="none" stroke="#888" stroke-width="1.2"/><path d="M5.5 4.5c.5-.5 1-.5 1.3 0l.7 1.2c.2.4 0 .7-.3 1l-.4.3c.4 1 1.1 1.7 2.1 2.1l.3-.4c.3-.3.6-.5 1-.3l1.2.7c.5.3.5.8 0 1.3-1.4 1.3-6.4-3.1-5.9-5.900z" fill="#888"/></svg>
  0800 555 019</div>
<div class="abs contact-line" style="top:47px">
  <svg width="16" height="16" viewBox="0 0 16 16"><circle cx="6" cy="7" r="3" fill="none" stroke="#888" stroke-width="1.2"/><path d="M1.5 14c.5-2.5 2.2-3.5 4.5-3.5s4 1 4.5 3.5" fill="none" stroke="#888" stroke-width="1.2"/><rect x="9" y="2" width="6" height="4" rx="1" fill="none" stroke="#888"/></svg>
  Live Chat</div>

<nav class="abs nav">
  <a style="left:189px">ABOUT US</a>
  <a style="left:282px">RESIDENTIAL</a>
  <a style="left:384px">COMMERCIAL</a>
  <a style="left:484px">REAL ESTATE/STRATA</a>
  <a style="left:622px">CONTACT US/QUOTE</a>
  <a style="left:757px">BLOG</a>
</nav>

<h1 class="abs h-script" style="left:206px;top:150px">Welcome to GK - Property Maintenance</h1>
<div class="abs intro">
  <p>Sed ut perspiciatis unde omnis iste natus error sit voluptatem accusantium doloremque laudantium, totam rem aperiam, eaque ipsa quae ab illo inventore veritatis.</p>
  <p>Nemo enim ipsam voluptatem quia voluptas sit aspernatur auodiaugitquisquamest. dolorem ipsum quia.</p>
</div>
<div class="abs hero-photo" role="img" aria-label="Photo of two smiling cleaners in aprons holding a spray bottle, broom and dustpan, in front of a faint clock face"></div>

<main class="abs panel"></main>

<h2 class="abs h-script" style="left:223px;top:350px;font-size:17.5px">Residential Focus : <em>WorkView</em></h2>
<div class="abs rule" style="left:223px;top:384px;width:370px"></div>
<div class="abs seal" role="img" aria-label="Round gold award seal"></div>
<div class="abs body-copy" style="left:223px;top:404px">
  <p style="width:360px">Quis autem vel eum iure reprehenderit qui in ea voluptate velit esse consequatur, vel illum qui dolorem eum fugiat quo voluptas nulla pariatur?</p>
  <p style="margin-top:12.8px">At vero eos et accusamus et iusto odio dignissimos ducimus qui blanditiis praesentium voluptatum deleniti atque corrupti quos dolores et quas molestias excepturi sint occaecati cupiditate non provident, similique sunt in culpa qui officia deserunt mollitia animi, id est laborum et dolorum fuga.</p>
</div>
<div class="abs thumb" style="left:218px"><span role="img" aria-label="Worker polishing an office floor" style="background:linear-gradient(#e8e2a8,#c9c38a)"></span></div>
<div class="abs thumb" style="left:331px"><span role="img" aria-label="Tradesman working at a bench" style="background:linear-gradient(#b89066,#4a4558)"></span></div>
<div class="abs thumb" style="left:446px"><span role="img" aria-label="Gloved hands cleaning a surface" style="background:linear-gradient(135deg,#6e7a3a,#3b2a1e,#c9a640)"></span></div>
<div class="abs thumb" style="left:564px"><span role="img" aria-label="Tradesman fixing a ceiling panel" style="background:linear-gradient(#eceff2,#6f86a8)"></span></div>

<h2 class="abs h-script" style="left:223px;top:622px;font-size:17.5px">About <em>Us</em></h2>
<div class="abs rule" style="left:223px;top:657px;width:420px"></div>
<div class="abs body-copy" style="left:222px;top:692px">
  <p>Nemo enim ipsam voluptatem quia voluptas sit aspernatur aut odit aut fugit, sed quia consequuntur magni dolores eos qui ratione voluptatem sequi nesciunt.</p>
  <p style="margin-top:12px">Neque porro quisquam est, qui dolorem ipsum quia dolor sit amet, consectetur, adipisci velit, sed quia non numquam eius modi tempora incidunt ut labore et dolore magnam aliquam quaerat voluptatem.</p>
  <p style="margin-top:12px">Ut enim ad minima veniam, quis nostrum exercitationem ullam corporis suscipit labo-riosam, nisi ut aliquid ex ea commodi consequatur?</p>
  <p style="margin-top:12px">Quis autem vel eum iure reprehenderit qui in ea voluptate velit esse quam nihil molestiae consequatur, vel illum qui dolorem eum fugiat quo voluptas nulla pariatur? .</p>
</div>

<div class="abs" style="left:716px;top:384px;height:487px;border-left:1px dotted #c4c4c4"></div>

<aside class="abs quote">
  <h2 class="abs h-script" style="left:15px;top:8px;font-size:18px">Get a <em>Quote</em></h2>
  <p class="abs" style="left:18px;top:41px;font-size:8.5px;color:#333">A GK specialist will get back to you.</p>
  <div class="field" style="left:14px;top:63px;width:86px"></div>
  <div class="field" style="left:105px;top:63px;width:67px"></div>
  <span class="lbl" style="left:14px;top:80px">FULL NAME</span>
  <span class="lbl" style="left:105px;top:80px">COMPANY</span>
  <div class="field" style="left:14px;top:97px;width:86px">you@mail.net</div>
  <div class="field" style="left:105px;top:97px;width:67px"></div>
  <span class="lbl" style="left:14px;top:114px">EMAIL</span>
  <span class="lbl" style="left:105px;top:114px">PHONE</span>
  <div class="select">Agency<i>&#9650;</i></div>
  <div class="submit">SUBMIT</div>
  <span class="abs" style="left:83px;top:157px;font-size:8.5px;color:var(--link)">or call us today</span>
</aside>

<h2 class="abs h-script" style="left:774px;top:609px;font-size:18px">Latest <em>News</em></h2>
<div class="abs" style="left:771px;top:647px;width:204px;border-top:1px solid #e2e2e2"></div>

<div class="abs news-title" style="left:775px;top:674px">Lorem ipsum doloret</div>
<p class="abs news-text" style="left:776px;top:700px">Quis autem vel eum iure reprehenderit qui in ea voluptate velit esse quam nihil mole.</p>
<span class="abs more" style="left:931px;top:731px">read more</span>
<div class="abs" style="left:777px;top:766px;width:196px;border-top:1px solid #e2e2e2"></div>

<div class="abs news-title" style="left:777px;top:789px">Lorem ipsum doloret</div>
<p class="abs news-text" style="left:777px;top:815px">Quis autem vel eum iure reprehenderit qui in ea voluptate velit esse quam nihil mole.</p>
<span class="abs more" style="left:933px;top:846px">read more</span>

<div class="abs curl"></div>

<footer class="foot">
  <a style="left:220px">ABOUT US</a>
  <a style="left:331px">RESIDENTIAL</a>
  <a style="left:455px">COMMERCIAL</a>
  <a style="left:579px">REAL ESTATE/STRATA</a>
  <a style="left:745px">CONTACT US/QUOTE</a>
  <a style="left:908px">BLOG</a>
</footer>
</body>
</html>
```